Animal Horse & Bedding Company Needs a Website Coded & Designed

We need a website for a new animal bedding and feed company that is visually grabbing and vibrant. We would like to see a website that displays trust, quality and confidence. Needs to be responsive and mobile friendly for all browsers and coded for both Android & IOS. SEO is also important.

Joomla or Wordpress – must be both desktop and mobile friendly with fast page load speed. Need the ability to edit ourselves in Wordpress or Joomla.

Full details attached below with some layout and content ideas.

Coding

Coded - Design and coding required

Number of Pages Required

5+ page

Font styles to use
Sans Serif

Requirements
Must have
• Needs to be responsive and mobile friendly for all browsers and coded for both Android & IOS. SEO is also important.

Wordpress – must be both desktop and mobile friendly with fast page load speed. Need the ability to edit ourselves in Wordpress.

Logo Colours:
Dark Brown
CMYK: 50 / 70 / 80 / 70
Pantone: 4625C

Orange
CMYK: 0 / 50 / 100 / 0
Pantone: 144C
Nice to have
• Use picture of building attached and super impose logo on building.

```html
<!DOCTYPE html>
<html lang="en">
<head>
<meta charset="utf-8">
<title>Golden Stem – Bedding &amp; Feed</title>
<link href="https://fonts.googleapis.com/css2?family=Poppins:wght@400;500;600;700&display=swap" rel="stylesheet">
<style>
:root{
  --brown:#3b160e;
  --brown-deep:#2a0f09;
  --orange:#f0890f;
  --orange-dark:#e07410;
  --ink:#222;
  --muted:#555;
  --paper:#ffffff;
  --stage:#f3f1ee;
}
*{box-sizing:border-box;margin:0;padding:0}
html,body{width:1200px;height:2866px;overflow:hidden}
body{background:var(--stage);font-family:'Poppins',sans-serif;color:var(--ink)}
.page{position:absolute;left:270px;top:0;width:660px;height:2866px;background:var(--paper);overflow:hidden;box-shadow:0 0 30px rgba(0,0,0,.12)}
section,header,footer{position:absolute;left:0;width:660px}
.abs{position:absolute}
.btn{position:absolute;background:var(--orange-dark);color:#fff;font-size:6px;font-weight:500;text-transform:uppercase;display:flex;align-items:center;justify-content:center;letter-spacing:.3px}
.photo{position:absolute}

/* hero */
.hero{top:0;height:325px;background:linear-gradient(180deg,#6b5a4a 0%,#a77b3c 28%,#b98a3c 55%,#9a6f2c 100%)}
.hero-horse{left:400px;top:60px;width:240px;height:265px;background:radial-gradient(ellipse at 50% 45%,#7a3614 0%,#8e4a1c 40%,rgba(160,110,50,0) 72%)}
.brand{position:absolute;left:68px;top:30px;display:flex;align-items:center;gap:7px;color:#fff;font-size:15px;font-weight:600;letter-spacing:1px}
.brand .dot{width:12px;height:12px;border-radius:50%;background:var(--orange)}
.topbar{position:absolute;right:69px;top:0;height:29px;display:flex;align-items:center;gap:22px;color:#fff;font-size:6px}
.topbar span{display:flex;align-items:center;gap:6px}
.quote-tab{position:absolute;right:0;top:0;width:69px;height:29px;background:var(--orange);display:flex;align-items:center;color:#fff;font-size:6px}
.quote-tab i{width:14px;height:29px;background:var(--brown);display:flex;align-items:center;justify-content:center;font-style:normal;font-size:9px;margin-right:7px}
.nav{position:absolute;left:278px;top:33px;width:382px;height:31px;background:rgba(40,30,25,.72);display:flex;color:#eee;font-size:7.5px}
.nav a{flex:1;display:flex;align-items:center;justify-content:center;border-right:1px solid rgba(255,255,255,.18);text-decoration:none;color:inherit}
.hero h1{position:absolute;left:63px;top:110px;color:#fff;font-size:24px;line-height:27px;font-weight:700;text-transform:uppercase}
.hero h1 em{font-style:normal;color:var(--orange)}
.hero .tag{position:absolute;left:66px;top:170px;color:#fff;font-size:16px;line-height:20px;font-weight:500;text-transform:uppercase}
.hero .btn{left:69px;top:229px;width:93px;height:25px;font-size:7px;background:var(--orange)}
.dots{position:absolute;left:70px;top:277px;display:flex;gap:6px}
.dots b{width:6px;height:6px;border-radius:50%;background:var(--orange)}
.dots b:first-child{background:none;border:1px solid var(--orange)}

/* section headings */
.h2{position:absolute;font-size:15px;font-weight:600;color:var(--ink)}
.h2::after{content:"";position:absolute;left:0;bottom:-5px;width:60px;height:2px;background:var(--orange)}
.h2.light{color:#fff}
.h2.caps{text-transform:uppercase;font-size:14px}
.body-text{position:absolute;font-size:6.4px;line-height:11.5px;color:var(--muted)}

/* about */
.about{top:325px;height:251px;background:#fff}
.about-mark{left:80px;top:30px;width:130px;height:130px;border-radius:50%;background:#f7efe6;display:flex;align-items:center;justify-content:center;color:var(--orange);font-size:15px;font-weight:600}

/* kind */
.kind{top:576px;height:252px;background:var(--brown)}
.kind .h2{font-size:15px;line-height:17px}
.kind .body-text{color:#e8d9d2;line-height:13.7px}
.grid-photo{width:109px;height:92px}

/* feeding */
.feeding{top:828px;height:282px;background:#fff}
.ticks{position:absolute;list-style:none;font-size:6.4px;color:var(--ink)}
.ticks li{position:relative;padding-left:12px;height:15.5px}
.ticks li::before{content:"";position:absolute;left:0;top:3px;width:4px;height:4px;border-radius:50%;background:var(--orange)}

/* bedding benefits */
.bedding{top:1110px;height:276px;background:linear-gradient(100deg,#3d2a10 0%,#6b4c1a 40%,#8a6420 70%,#5a3e14 100%)}
.bedding .ticks{color:#f2e8d8}
.bedding .ticks li{height:14.3px}

/* bulk */
.bulk{top:1386px;height:321px;background:#fff}
.service{position:absolute;width:130px;text-align:center}
.service h3{font-size:7px;font-weight:600;text-transform:uppercase;margin-bottom:16px}
.service svg{display:block;margin:0 auto 20px}
.service p{font-size:6.2px;line-height:11.5px;color:var(--muted)}

/* products */
.products{top:1707px;height:481px;background:var(--brown)}
.card{position:absolute;width:166px;height:143px}
.card .label{height:23px;background:var(--orange);color:#fff;font-size:8px;display:flex;align-items:center;justify-content:center;text-transform:uppercase}
.card .photo{position:relative;height:120px}

/* testimonials */
.testimonials{top:2188px;height:478px;background:#fff}
.testimonials h2{position:absolute;left:0;width:660px;top:45px;text-align:center;font-size:14px;font-weight:600}
.quote{position:absolute;top:103px;width:169px;height:215px;background:#fff;box-shadow:0 2px 10px rgba(0,0,0,.14);text-align:center}
.quote .stars{margin-top:24px;color:var(--orange-dark);font-size:10px;letter-spacing:2px}
.quote p{margin:4px 18px 0;font-size:6.2px;line-height:10.5px;color:var(--ink)}
.quote .avatar{width:28px;height:28px;border-radius:50%;margin:10px auto 0;background:linear-gradient(#c9b6a6,#7d6a5c)}
.quote h4{margin-top:6px;font-size:6px;font-weight:600}
.quote small{display:block;margin-top:5px;font-size:5px;color:var(--orange-dark)}

/* newsletter */
.newsletter{position:absolute;left:43px;top:2609px;width:598px;height:55px;background:var(--orange-dark);z-index:2}
.newsletter .label{position:absolute;left:24px;top:22px;color:#fff;font-size:8px}
.newsletter .field{position:absolute;left:159px;top:16px;width:298px;height:27px;background:#fff;color:#999;font-size:8px;padding-left:14px;display:flex;align-items:center}
.newsletter .go{position:absolute;left:457px;top:16px;width:88px;height:27px;background:var(--brown-deep);color:#fff;font-size:8px;display:flex;align-items:center;justify-content:center}

/* footer */
.site-footer{top:2646px;height:220px;background:var(--brown)}
.foot-brand{position:absolute;left:44px;top:42px;display:flex;align-items:center;gap:5px;color:#fff;font-size:11px;font-weight:600;letter-spacing:.5px}
.foot-brand .dot{width:9px;height:9px;border-radius:50%;background:var(--orange)}
.foot-about{position:absolute;left:37px;top:90px;width:140px;font-size:6px;line-height:10.5px;color:#e6d6cd}
.socials{position:absolute;left:44px;top:149px;display:flex;gap:14px}
.socials b{width:10px;height:10px;border-radius:50%;border:1px solid #fff}
.foot-col{position:absolute;color:#fff}
.foot-col h5{font-size:9.5px;font-weight:500;text-transform:uppercase;margin-bottom:8px}
.foot-col ul{list-style:none;font-size:6px}
.foot-col li{position:relative;padding-left:18px}
.foot-col li::before{content:"";position:absolute;left:0;top:3px;width:3px;height:3px;border-radius:50%;background:var(--orange)}
.contact{position:absolute;left:471px;top:56px;color:#fff}
.contact h5{font-size:11px;font-weight:400}
.contact .phone{color:var(--orange);font-size:12px;margin-top:2px}
.contact p{display:flex;align-items:center;gap:10px;font-size:10px;margin-top:14px}
.rule{position:absolute;left:37px;top:194px;width:586px;height:1px;background:rgba(255,255,255,.25)}
.copy{position:absolute;left:0;width:660px;top:200px;text-align:center;color:#e6d6cd;font-size:6px}
</style>
</head>
<body>
<div class="page">

  <header class="hero">
    <div class="photo hero-horse" role="img" aria-label="Chestnut horse galloping through a golden field"></div>
    <div class="brand"><span class="dot"></span>GOLDEN STEM</div>
    <div class="topbar">
      <span><svg width="8" height="8" viewBox="0 0 10 10"><path d="M2 1l2 2-1 1.5c.6 1.2 1.4 2 2.5 2.5L7 6l2 2-1.3 1.3C4.5 9 1 5.5.7 2.3z" fill="#fff"/></svg>555-0142-778</span>
      <span><svg width="10" height="7" viewBox="0 0 10 7"><rect width="10" height="7" fill="#fff"/><path d="M0 0l5 4 5-4" stroke="#777" fill="none"/></svg>goldenstemfarm.com</span>
    </div>
    <div class="quote-tab"><i>›</i>Request a<br>Quote</div>
    <nav class="nav"><a>Home</a><a>Feed</a><a>Bedding</a><a>About Us</a><a>Contact us</a></nav>
    <h1>Welcome to <em>Animals</em><br><em>Bedding</em> Company</h1>
    <p class="tag">Fieldhome Pets make life<br>better!</p>
    <div class="btn">Request a quote</div>
    <div class="dots"><b></b><b></b><b></b><b></b><b></b></div>
  </header>

  <section class="about">
    <div class="abs about-mark">Golden Stem</div>
    <h2 class="h2" style="left:302px;top:45px">About us</h2>
    <div class="body-text" style="left:298px;top:79px;width:300px">
      The Golden Stem is a locally owned company located in Millbrook, AB. We<br>are dedicated in providing high quality products and services.<br>
      <span style="display:block;margin-top:3px">Producing, buying and marketing hay and straw for x amount of years.<br>Insert blurb on ownership/history of key staff/owners.</span>
      <span style="display:block;margin-top:3px">The Golden Stem offers supply and delivery of fresh bedding as well as removal of<br>waste bedding. Let us deliver you a container of fresh straw and haul your waste<br>bedding away. A full service solution that is sustainable and responsible.</span>
    </div>
    <div class="btn" style="left:298px;top:187px;width:77px;height:18px">View more</div>
  </section>

  <section class="kind">
    <h2 class="h2 light" style="left:42px;top:30px">The bedding that’s kind to<br>your animals</h2>
    <p class="body-text" style="left:42px;top:86px;width:265px">Your animal deserves the very best in health and comfort to keep them healthy, strong and happy. Our products are designed for horses, livestock (goats, cattle and sheep), small caged animals (rabbits, guinea pigs and more). Your animal deserves the very best in health and comfort to keep them healthy, strong and happy. Our products are designed for horses, livestock (goats, cattle and sheep), small caged animals (rabbits, guinea pigs and more).</p>
    <p class="body-text" style="left:42px;top:192px;width:250px;line-height:12px">QUALITY GUARANTEED Grown for quality - 100% natural with no chemicals or additives</p>
    <div class="photo grid-photo" style="left:385px;top:34px;background:linear-gradient(#7d8a4a,#5a6a2e)" role="img" aria-label="Rabbit sitting on grass"></div>
    <div class="photo grid-photo" style="left:502px;top:34px;background:linear-gradient(#c9917c,#a8705a)" role="img" aria-label="Piglets resting on straw"></div>
    <div class="photo grid-photo" style="left:385px;top:131px;background:linear-gradient(#6a6e70,#2c2f32)" role="img" aria-label="Cat eating from a bowl"></div>
    <div class="photo grid-photo" style="left:502px;top:131px;background:linear-gradient(#9aa46a,#e8e2d4)" role="img" aria-label="Lamb lying on grass"></div>
  </section>

  <section class="feeding">
    <div class="photo" style="left:42px;top:60px;width:278px;height:182px;background:linear-gradient(135deg,#c46a2a,#6a3a1e 55%,#3a2a20)" role="img" aria-label="White horse running in a paddock at sunset"></div>
    <h2 class="h2 caps" style="left:371px;top:60px">Feeding benefits</h2>
    <ul class="ticks" style="left:373px;top:99px">
      <li>100% Natural Chopped Straw</li><li>Low Dust</li><li>Chemical &amp; Additive Free</li><li>Clean &amp; Highly Absorbent</li><li>Cheaper than Wood Shavings</li><li>Economic – less used and less wasted</li><li>Environmentally Friendly – Recyclable &amp; Compostable</li>
    </ul>
    <div class="btn" style="left:385px;top:217px;width:77px;height:17px;background:var(--orange)">View more</div>
  </section>

  <section class="bedding" role="img" aria-label="Brown rabbit sitting in autumn grass">
    <h2 class="h2 caps light" style="left:97px;top:40px">Bedding benefits</h2>
    <ul class="ticks" style="left:100px;top:91px">
      <li>100% Natural</li><li>Chemical &amp; Additive Free</li><li>Available in Pellets or Cubes</li><li>High Protein Content</li><li>Eliminate Waste in Feeding</li><li>Clean – Eliminates Dust From Feeding Baled Hay</li><li>Cost Effective</li><li>Convenient</li><li>Less wasted feed</li>
    </ul>
    <div class="btn" style="left:112px;top:224px;width:76px;height:18px;background:var(--orange)">View more</div>
  </section>

  <section class="bulk">
    <h2 class="h2" style="left:50px;top:46px">Bulk pricing and delivery</h2>
    <div class="service" style="left:55px;top:93px">
      <h3>Online shop</h3>
      <svg width="46" height="40" viewBox="0 0 46 40" fill="none" stroke="#f0890f" stroke-width="2"><rect x="4" y="3" width="38" height="26"/><path d="M18 34h10M23 29v5"/><path d="M14 10h3l3 9h10l2-7H18"/><circle cx="21" cy="22" r="1.5"/><circle cx="29" cy="22" r="1.5"/></svg>
      <p>Offering a variety of animal feeds through our online shop. If you would like us to add something to our online shop, please contact us.</p>
    </div>
    <div class="service" style="left:266px;top:93px">
      <h3>Deliveries</h3>
      <svg width="46" height="44" viewBox="0 0 46 44" fill="none" stroke="#f0890f" stroke-width="2"><rect x="14" y="3" width="28" height="26"/><path d="M24 3v8h8V3"/><path d="M4 26l10-4 10 6h8v4H20"/><path d="M4 36l12 2 16-6"/></svg>
      <p>For a small fee we can deliver your pet feed order. Just place your order online or on the website and we will call with a delivery time and date</p>
    </div>
    <div class="service" style="left:471px;top:93px">
      <h3>Feed advice</h3>
      <svg width="40" height="46" viewBox="0 0 40 46" fill="none" stroke="#f0890f" stroke-width="2"><path d="M6 4h28a3 3 0 013 3v26a3 3 0 01-3 3H20l-8 7v-7H6a3 3 0 01-3-3V7a3 3 0 013-3z"/><circle cx="20" cy="23" r="5"/><circle cx="13" cy="15" r="1.5"/><circle cx="27" cy="15" r="1.5"/></svg>
      <p>With experienced staff in store, we can provide help and information to help you decide on which feed may best suit your horses specific dietary needs.</p>
    </div>
    <div class="btn" style="left:292px;top:268px;width:78px;height:17px">Request quote</div>
  </section>

  <section class="products">
    <h2 class="h2 caps light" style="left:43px;top:30px">Our product for</h2>
    <div class="card" style="left:43px;top:93px"><div class="label">Pig</div><div class="photo" style="background:linear-gradient(#d8a89a,#8a6a52)" role="img" aria-label="Pig in a pen"></div></div>
    <div class="card" style="left:249px;top:93px"><div class="label">Hourse</div><div class="photo" style="background:linear-gradient(#3a3430,#201c1a)" role="img" aria-label="White horse in a dark barn"><div class="btn" style="left:58px;top:48px;width:50px;height:11px;font-size:4.5px">Add to cart</div></div></div>
    <div class="card" style="left:454px;top:93px"><div class="label">Rabbit</div><div class="photo" style="background:linear-gradient(#4e6a3a,#a8a89a)" role="img" aria-label="White rabbit on grass"></div></div>
    <div class="card" style="left:43px;top:263px"><div class="label">Goat</div><div class="photo" style="background:linear-gradient(#6a6a64,#d8d6cc)" role="img" aria-label="White goat in a pen"></div></div>
    <div class="card" style="left:249px;top:263px"><div class="label">Small caged animals</div><div class="photo" style="background:linear-gradient(#2a2a2e,#6a7486)" role="img" aria-label="Grey parrot in a cage"></div></div>
    <div class="card" style="left:454px;top:263px"><div class="label">Dog</div><div class="photo" style="background:linear-gradient(#5a4a44,#b06a3a)" role="img" aria-label="Dog resting on a blanket"></div></div>
    <div class="btn" style="left:292px;top:433px;width:78px;height:17px">View more more</div>
  </section>

  <section class="testimonials">
    <h2>TESTIMONIAL</h2>
    <div class="quote" style="left:30px"><div class="stars">★★★★★</div><p>lorem ipsum dolor sit amet, consectetur adipiscing elit. nulla sed cum nunc, egestas placerat vulputate id vitae. a id pellentesque suspendisse tortor mi elementum interdum mauris venenatis.</p><div class="avatar" role="img" aria-label="Customer portrait"></div><h4>DANIEL REEVE</h4><small>FAIRVIEW, MN</small></div>
    <div class="quote" style="left:245px"><div class="stars">★★★★★</div><p>lorem ipsum dolor sit amet, consectetur adipiscing elit. nulla sed cum nunc, egestas placerat vulputate id vitae. a id pellentesque suspendisse tortor mi elementum interdum mauris venenatis.</p><div class="avatar" role="img" aria-label="Customer portrait"></div><h4>DANIEL REEVE</h4><small>FAIRVIEW, MN</small></div>
    <div class="quote" style="left:461px"><div class="stars">★★★★★</div><p>lorem ipsum dolor sit amet, consectetur adipiscing elit. nulla sed cum nunc, egestas placerat vulputate id vitae. a id pellentesque suspendisse tortor mi elementum interdum mauris venenatis.</p><div class="avatar" role="img" aria-label="Customer portrait"></div><h4>DANIEL REEVE</h4><small>FAIRVIEW, MN</small></div>
    <div class="btn" style="left:297px;top:358px;width:78px;height:17px">View more more</div>
  </section>

  <div class="newsletter">
    <span class="label">Subscribe Our Newsletter</span>
    <div class="field">Enter your email</div>
    <div class="go">Subscribe</div>
  </div>

  <footer class="site-footer">
    <div class="foot-brand"><span class="dot"></span>GOLDEN STEM</div>
    <p class="foot-about">The Golden Stem is a locally owned company located in Millbrook, AB. We are dedicated in providing high quality products and services.</p>
    <div class="socials"><b></b><b></b><b></b><b></b></div>
    <div class="foot-col" style="left:199px;top:56px"><h5>Products</h5><ul style="line-height:12.9px"><li>Cats</li><li>Dog</li><li>Rabit</li><li>Birds</li><li>sheep</li><li>pigs</li></ul></div>
    <div class="foot-col" style="left:329px;top:54px"><h5>Customer care</h5><ul style="line-height:16.5px"><li>Home</li><li>Our Services</li><li>blog</li><li>About us</li><li>Contact Us</li></ul></div>
    <div class="contact">
      <h5>Call Now For Services!</h5>
      <div class="phone">555-642-0198</div>
      <p><svg width="11" height="8" viewBox="0 0 11 8" fill="none" stroke="#fff"><rect x=".5" y=".5" width="10" height="7"/><path d="M.5.5l5 4 5-4"/></svg>Email Us</p>
      <p><svg width="9" height="12" viewBox="0 0 9 12" fill="none" stroke="#fff"><path d="M4.5 11.5S.5 7 .5 4.5a4 4 0 018 0c0 2.5-4 7-4 7z"/><circle cx="4.5" cy="4.5" r="1.5"/></svg>Get Direction</p>
    </div>
    <div class="rule"></div>
    <p class="copy">the golden stem © 2021 All Rights Reserved. Terms of Use and Privacy Policy</p>
  </footer>

</div>
</body>
</html>
```